Harlow Advisory, Business Cards for International Development Consultancy

I'm an independent consultant working in the international development sector. I work with small organisations in developing countries to help them develop their community based programs so that they can be internationally competitive. This means they need to work better with their own communities to deliver meaningful quality work and also improve the accountability of their work so that they can compete for international and domestic funding.

I like the idea of being a connector between community, local organisations and international best practice and back again (ie acknowledging that international best practice can learn a lot from community).

My surname is Harlow - so I'd like the logo to use the idea of web as a connector.

I work with people with sight impairments - would like my card to be useful for low vision (i.e. clear graphics, easy to read font) and no vision (i.e. brail).

Target Market(s)

international non-government organisations (i.e. pelmark, lift the hamlets, kindred arc), Blue Shield Gold Lantern, government (i.e. Australian Bureau of Overseas Relations, consulars), non government agencies,

Industry/Entity Type

Business

Contact Information for Business Card

International Development Consultant
Connecting International Development with Community

Marcia Harlow
Lead Consultant
Phone: +61 412 583720
Email: mharlow.advisory@postnest.example

Font styles to use
Sans Serif

Colors
eaf1f7
85acd3
d3a5cc
0456a4
a64599
0255a3

Requirements
Nice to have
• brail
Should not have
• fancy fonts - needs to be easy to read.

```html
<!DOCTYPE html>
<html lang="en">
<head>
<meta charset="utf-8">
<title>Harlow Advisory – Business Cards</title>
<link rel="stylesheet" href="https://fonts.googleapis.com/css2?family=Questrial&display=swap">
<style>
  :root {
    --page-bg: #e6e8eb;
    --card-white: #f7f7f5;
    --ink: #1c1c1c;
    --brand-blue: #0456a4;
    --accent-blue: #2f7cc4;
    --mark-blue: #8ea8cf;
    --back-blue-light: #2462b0;
    --back-blue-dark: #174c93;
    --silver: #c9ced6;
  }
  * { margin: 0; padding: 0; box-sizing: border-box; }
  html, body {
    width: 1200px; height: 968px; overflow: hidden;
    background: var(--page-bg);
    font-family: "Questrial", sans-serif;
  }
  .sheet {
    width: 1200px; height: 968px;
    display: flex; flex-direction: column; align-items: center; justify-content: center;
    gap: 56px;
  }
  .card {
    width: 660px; height: 378px;
    border-radius: 26px;
    position: relative;
    box-shadow: 0 6px 18px rgba(0,0,0,0.14);
  }
  /* front */
  .card-front {
    background: var(--card-white);
    display: flex; flex-direction: column; align-items: center;
    padding-top: 62px;
  }
  .brand-name {
    font-size: 34px; color: var(--mark-blue); letter-spacing: 1px;
  }
  .person-name {
    margin-top: 44px; font-size: 30px; color: var(--ink);
  }
  .person-role {
    margin-top: 2px; font-size: 17px; color: var(--accent-blue);
  }
  .contact-row {
    margin-top: 22px; display: flex; align-items: center; gap: 18px;
    font-size: 17px; color: var(--ink);
  }
  .contact-item { display: flex; align-items: center; gap: 8px; }
  .contact-icon { width: 24px; height: 18px; fill: var(--brand-blue); }
  .tagline {
    margin-top: 22px; font-size: 20px; color: var(--accent-blue);
  }
  /* back */
  .card-back {
    background: linear-gradient(160deg, var(--back-blue-light), var(--back-blue-dark));
    display: flex; align-items: center; justify-content: center;
  }
  .back-brand {
    font-size: 40px; color: var(--silver);
    letter-spacing: 8px; text-transform: uppercase;
  }
</style>
</head>
<body>
<main class="sheet">
  <section class="card card-front" aria-label="Business card front">
    <div class="brand-name">Harlow Advisory</div>
    <div class="person-name">Marcia Harlow</div>
    <div class="person-role">Lead Consultant</div>
    <div class="contact-row">
      <span class="contact-item">
        <svg class="contact-icon" viewBox="0 0 24 18" aria-hidden="true">
          <path d="M2 6 C2 2 22 2 22 6 L22 8 L17 8 L17 6 L7 6 L7 8 L2 8 Z"/>
          <path d="M6 8 L18 8 L21 17 L3 17 Z"/>
          <circle cx="12" cy="12.5" r="2.6" fill="#f7f7f5"/>
        </svg>
        +61 412 583720
      </span>
      <span class="contact-item">
        <svg class="contact-icon" viewBox="0 0 24 18" aria-hidden="true">
          <rect x="1" y="2" width="22" height="14" rx="1"/>
          <path d="M1.5 2.5 L12 10 L22.5 2.5" fill="none" stroke="#f7f7f5" stroke-width="1.6"/>
        </svg>
        mharlow.advisory@postnest.example
      </span>
    </div>
    <div class="tagline">Connecting International Development with Community</div>
  </section>

  <section class="card card-back" aria-label="Business card back">
    <div class="back-brand">Harlow Advisory</div>
  </section>
</main>
</body>
</html>
```